Refer a Friend A5 Flyer for Healthcare Staff

We need an A5 flyer that we can hand out to existing and new staff members promoting our Refer a friend Scheme. We need the leaflet to encourage staff to talk to their family and friends about joining our Healthcare Agency, which provides staff to local care related establishments. Using our logo and brand colours blue and green, as per our website, the final design will need to clearly convey the benefits and attractions of referring additional staff to the team. In addition is the promotion of our Chatterbook page, requesting staff to like the page and to like and share various posts.

Target Market(s)

Healthcare and potential Healthcare Staff

Industry/Entity Type

Healthcare

Colors
33b8a4
3277b5

Requirements
Must have
• Company Logo, Brand colours,
• text; "Refer a Friend and receive a £50 Bonus after just 1 completed shift"
• text; "3 easy steps to refer a friend, 1 Fill out your name on the back of your Business Card 2 Hand the card to your friend or any person you wish to refer, 3 ask your friend to present the card to us when they attend their interview"
• text; "Like and share any of our Open Days on Chatterbook for a chance to win a prize, you can find us easily by searching @CarewellStaffingPartners"
• text; "Like our Page to stay up to date with our events and offers"
Nice to have
• care worker / elderly care / support worker pictures
• Content / pics from website www.carewellstaffingpartners.co.uk

```html
<!DOCTYPE html>
<html lang="en">
<head>
<meta charset="utf-8">
<title>Carewell Staffing – Refer a Friend</title>
<link rel="stylesheet" href="https://fonts.googleapis.com/css2?family=Montserrat:wght@400;500;700&family=Roboto:wght@500&display=swap">
<style>
  :root {
    --brand-blue: #1a4f9c;
    --brand-blue-deep: #154585;
    --brand-green: #1a9a80;
    --brand-green-dark: #168a72;
    --panel-edge: #d9dcdc;
    --ink: #2b2f36;
    --paper: #f4f5f5;
    --white: #ffffff;
  }
  html, body {
    margin: 0;
    padding: 0;
    width: 872px;
    height: 1200px;
    overflow: hidden;
    background: var(--paper);
  }
  .flyer {
    position: relative;
    width: 872px;
    height: 1200px;
    overflow: hidden;
    background: linear-gradient(180deg, #ffffff 0%, #eceeee 100%);
    font-family: "Montserrat", Arial, sans-serif;
  }
  .hero-photo {
    position: absolute;
    left: 0; top: 0;
    width: 872px; height: 560px;
    background:
      linear-gradient(90deg, rgba(255,255,255,0) 0%, rgba(255,255,255,0) 40%, rgba(255,255,255,0.85) 62%, #f7f8f7 80%),
      linear-gradient(160deg, #4f6b35 0%, #7c9a55 30%, #a9b98a 55%, #d6ddd0 80%);
  }
  .waves { position: absolute; left: 0; top: 0; }
  .brand {
    position: absolute;
    right: 52px; top: 90px;
    display: flex;
    align-items: center;
    gap: 14px;
  }
  .brand-mark {
    width: 30px; height: 30px;
    border-radius: 50%;
    background: var(--brand-green);
  }
  .brand-name {
    margin: 0;
    text-align: right;
    font-weight: 500;
    font-size: 46px;
    line-height: 1.05;
    color: var(--brand-blue);
  }
  .offer {
    position: absolute;
    right: 50px; top: 268px;
    margin: 0;
    text-align: right;
    font-weight: 700;
    font-size: 22.5px;
    line-height: 1.33;
    letter-spacing: -0.3px;
    color: var(--brand-blue);
  }
  .steps-title {
    position: absolute;
    left: 58px; top: 460px;
    margin: 0;
    font-weight: 700;
    font-size: 28px;
    line-height: 1.12;
    color: var(--brand-blue);
  }
  .steps-title .accent { color: var(--brand-green); display: block; margin-top: 4px; }
  .steps {
    position: absolute;
    left: 32px; top: 563px;
    width: 412px;
    margin: 0; padding: 0;
    list-style: none;
    font-family: "Roboto", Arial, sans-serif;
    font-weight: 500;
    font-size: 15px;
    line-height: 22px;
    letter-spacing: 0.3px;
    color: var(--ink);
  }
  .steps li {
    display: flex;
    gap: 8px;
    margin-bottom: 16px;
  }
  .step-num {
    flex: none;
    width: 18px; height: 18px;
    margin-top: 2px;
    border-radius: 50%;
    background: var(--brand-blue);
    color: var(--white);
    font-size: 11px;
    line-height: 18px;
    text-align: center;
  }
  .social {
    position: absolute;
    left: 35px;
    margin: 0;
    font-weight: 700;
    font-size: 15px;
    line-height: 23px;
    letter-spacing: -0.3px;
    color: var(--brand-blue);
    text-transform: uppercase;
    white-space: nowrap;
  }
  .social-share { top: 746px; }
  .social-find { top: 838px; left: 37px; }
  .social-find .handle { color: var(--brand-green); }
  .like-badge {
    position: absolute;
    left: 350px; top: 744px;
    width: 70px; height: 82px;
    border-radius: 8px;
    background: linear-gradient(160deg, #2fb197 0%, #1a9a80 100%);
  }
  .like-page {
    position: absolute;
    left: 37px; top: 902px;
    margin: 0;
    font-weight: 700;
    font-size: 23px;
    line-height: 34px;
    letter-spacing: -0.3px;
    color: var(--brand-blue);
    text-transform: uppercase;
  }
  .contact-panel {
    position: absolute;
    left: 453px; top: 453px;
    width: 342px; height: 588px;
    border: 2px solid var(--panel-edge);
    border-radius: 82px;
    overflow: hidden;
    background: linear-gradient(180deg, #1a9c82 0%, #168a72 100%);
    color: var(--white);
  }
  .contact-item {
    height: 190px;
    display: flex;
    flex-direction: column;
    align-items: center;
    justify-content: center;
    gap: 30px;
    border-bottom: 2px solid var(--panel-edge);
    font-size: 15px;
    letter-spacing: -0.1px;
  }
  .contact-item:first-child { padding-top: 14px; height: 176px; }
  .contact-item:last-child { border-bottom: 0; height: 204px; padding-bottom: 10px; box-sizing: border-box; }
  .contact-item.phone { font-size: 17px; }
  .contact-item svg { display: block; }
  .footer-note {
    position: absolute;
    left: 52px; top: 1114px;
    margin: 0;
    font-family: "Roboto", Arial, sans-serif;
    font-weight: 500;
    font-size: 19px;
    line-height: 1.27;
    color: #e9eef6;
  }
</style>
</head>
<body>
<main class="flyer">
  <div class="hero-photo" role="img" aria-label="Photo of a smiling care worker standing behind an elderly woman in a wheelchair in a sunny garden"></div>

  <svg class="waves" width="872" height="1200" viewBox="0 0 872 1200" aria-hidden="true">
    <path d="M0,379 C50,355 110,340 170,346 C280,356 380,430 460,480 L460,530 C380,488 290,430 200,408 C120,392 60,410 0,436 Z" fill="var(--brand-blue)"/>
    <path d="M0,436 C60,410 120,392 200,408 C290,430 380,488 460,530 L460,1000 L0,1000 Z" fill="#f1f2f2"/>
    <path d="M797,570 C830,555 855,530 872,500 L872,524 C855,554 830,578 797,590 Z" fill="var(--brand-blue)"/>
    <path d="M0,978 C50,1050 120,1085 220,1080 C340,1072 450,1010 560,985 C700,960 800,960 872,930 L872,1200 L0,1200 Z" fill="var(--brand-green)"/>
    <path d="M0,992 C50,1065 120,1100 220,1095 C340,1088 450,1030 560,1005 C700,982 800,985 872,965 L872,1200 L0,1200 Z" fill="var(--brand-blue-deep)"/>
  </svg>

  <div class="brand">
    <span class="brand-mark" aria-hidden="true"></span>
    <p class="brand-name">Carewell<br>Staffing</p>
  </div>

  <h1 class="offer">REFER A FRIEND AND&nbsp; RECEIVE<br>A £50 BONUS AFTER JUST 1<br>COMPLETED SHIFT</h1>

  <h2 class="steps-title">3 EASY STEPS<span class="accent">TO REFER A FRIEND</span></h2>

  <ol class="steps">
    <li><span class="step-num">1</span><span>Fill out your name on the back of your Business<br>Card</span></li>
    <li><span class="step-num">2</span><span>Hand the card to your friend or any person you<br>wish to refer</span></li>
    <li><span class="step-num">3</span><span>ask your friend to present the card to us when<br>they attend their interview</span></li>
  </ol>

  <p class="social social-share">Like and share any of our<br>open days on Chatterbook<br>for a chance to win a prize,</p>
  <div class="like-badge" role="img" aria-label="Thumbs-up like and share illustration"></div>
  <p class="social social-find">You can find us easily by<br>searching <span class="handle">@CarewellStaffingPartners</span></p>

  <p class="like-page">Like our page to stay up<br>to date with our events<br>and offers</p>

  <section class="contact-panel" aria-label="Contact details">
    <div class="contact-item phone">
      <svg width="40" height="40" viewBox="0 0 40 40" aria-hidden="true">
        <path d="M9 4 L15 4 L17 12 L13 15 C15 21 19 25 25 27 L28 23 L36 25 L36 31 C36 34 33 36 30 35 C17 32 8 23 5 10 C4 7 6 4 9 4 Z" fill="#ffffff"/>
        <path d="M23 10 A8 8 0 0 1 30 17" stroke="#ffffff" stroke-width="2.5" fill="none" stroke-linecap="round"/>
        <path d="M24 4 A14 14 0 0 1 36 16" stroke="#ffffff" stroke-width="2.5" fill="none" stroke-linecap="round"/>
      </svg>
      <span>020-555-0142</span>
    </div>
    <div class="contact-item web">
      <svg width="44" height="44" viewBox="0 0 44 44" aria-hidden="true" fill="none" stroke="#ffffff" stroke-width="3">
        <circle cx="22" cy="22" r="19"/>
        <ellipse cx="22" cy="22" rx="8" ry="19"/>
        <line x1="22" y1="3" x2="22" y2="41"/>
        <line x1="3" y1="22" x2="41" y2="22"/>
        <line x1="6" y1="13" x2="38" y2="13"/>
        <line x1="6" y1="31" x2="38" y2="31"/>
      </svg>
      <span>www.carewellstaffingpartners.co.uk</span>
    </div>
    <div class="contact-item mail">
      <svg width="52" height="30" viewBox="0 0 52 30" aria-hidden="true">
        <rect x="1" y="1" width="50" height="28" fill="#e9eceb" stroke="#c9cfcd"/>
        <path d="M1 1 L26 18 L51 1" fill="none" stroke="#9aa5a2" stroke-width="1.5"/>
        <path d="M1 29 L20 14 M51 29 L32 14" fill="none" stroke="#9aa5a2" stroke-width="1.5"/>
      </svg>
      <span>info@carewellstaffingpartners.co.uk</span>
    </div>
  </section>

  <p class="footer-note">We're Staffing Standards Council (SSC) registered<br>and an accredited National Living Wage Employer.</p>
</main>
</body>
</html>
```